need a Flyer for Plush Toy company

Need a Flyer for Plush Toy company ,

I upload a file for TEXT

Target Market(s)

Toys wholesalers , Supermarket

Industry/Entity Type

Toy Store

Colors
000000
ec1f27
c4c4c4

Requirements
Must have
• I have up loaded 3 files
• 1. Logo Registered Brand
• 2. customer's design in drawing
• 3. our ready samples based on Design
Nice to have
• happy kids in Nature ,
• happy kids in Ski ,
• different color Kids ,
• Multi culture concept

```html
<!DOCTYPE html>
<html lang="en">
<head>
<meta charset="utf-8">
<title>Tavo Toys – Plush Toy Flyer</title>
<link rel="stylesheet" href="https://fonts.googleapis.com/css2?family=Rubik:wght@500;700&family=Source+Sans+3:wght@400;600&family=Patrick+Hand&display=swap">
<style>
:root{
  --red:#ec1f27;
  --black:#111111;
  --grey:#c4c4c4;
  --paper:#f2f2f2;
  --white:#ffffff;
  --text:#1c1c1c;
}
*{margin:0;padding:0;box-sizing:border-box}
html,body{width:913px;height:1200px;overflow:hidden;background:var(--white)}
.flyer{position:relative;width:913px;height:1200px;overflow:hidden;background:var(--paper);font-family:"Source Sans 3",sans-serif;color:var(--text)}
.shapes{position:absolute;inset:0}
.brand{position:absolute;left:92px;top:112px;display:flex;align-items:center;gap:10px;font-family:"Rubik",sans-serif;font-weight:700;font-size:38px;color:var(--black)}
.brand-dot{width:22px;height:22px;border-radius:50%;background:var(--red)}
.tagline{position:absolute;left:22px;top:246px;font-family:"Patrick Hand",cursive;font-size:44px;color:var(--red);letter-spacing:-0.5px}
.photo{position:absolute}
.photo-kids{left:454px;top:-43px;width:480px;height:480px;border-radius:50%;
  background:
    radial-gradient(circle at 50% 50%,rgba(240,200,165,.95) 0%,rgba(214,160,120,.85) 28%,rgba(214,160,120,0) 52%),
    conic-gradient(from 200deg,#4f8fd0,#d8333a,#4a7fc4,#f2d23a,#f4e6e0,#d8333a,#7fb0e0,#4f8fd0);
  filter:saturate(.9)}
.photo-kids::after{content:"";position:absolute;inset:0;border-radius:50%;background:radial-gradient(circle,rgba(0,0,0,0) 60%,rgba(70,110,50,.55) 100%)}
.photo-baby{left:379px;top:269px;width:200px;height:200px;border-radius:50%;border:8px solid #e3e3e3;background:radial-gradient(circle at 45% 35%,#f3d6be 0%,#f5f0e8 40%,#e9e0d0 70%,#f0d25a 88%,#d9cfbf 100%)}
.photo-plush{left:530px;top:484px;width:350px;height:124px;border-radius:60px;
  background:linear-gradient(90deg,#f2b8cb 0%,#f6eee6 22%,#e7904e 40%,#b7a6d8 58%,#86c4e0 76%,#f4d236 100%);
  -webkit-mask:radial-gradient(ellipse at center,#000 55%,transparent 100%);
          mask:radial-gradient(ellipse at center,#000 55%,transparent 100%)}
.photo-sofa{left:27px;top:842px;width:444px;height:166px;border-radius:14px 14px 6px 6px;
  background:
    linear-gradient(90deg,#f6cfd8 6%,#c9d3e8 22%,#f4b073 38%,#f7f3ea 52%,#a9dbe6 68%,#f6e15a 82%) top/100% 62px no-repeat,
    linear-gradient(180deg,#a7d3a9 0%,#93c69b 70%,#86b88e 100%)}
.photo-sofa::after{content:"";position:absolute;left:0;right:0;top:62px;height:16px;background:linear-gradient(180deg,rgba(255,255,255,0),rgba(147,198,155,1))}
.intro{position:absolute;left:22px;top:460px;width:478px;text-align:center;font-family:"Rubik",sans-serif;font-weight:500;color:var(--red);font-size:23px;line-height:31.5px;letter-spacing:.4px}
.intro .name{font-size:24px}
.about{position:absolute;left:22px;top:620px;width:472px;font-size:18.5px;line-height:24px;letter-spacing:-0.4px}
.about p+p{margin-top:23px}
.line{display:block;text-align:justify;text-align-last:justify;white-space:nowrap}
.line.end{text-align-last:left}
.offer{position:absolute;left:518px;top:413px;width:372px;height:597px;background:var(--red);border-radius:0 0 16px 16px;box-shadow:0 4px 8px rgba(0,0,0,.18);color:var(--white)}
.offer-title{position:absolute;left:35px;top:208px;font-family:"Rubik",sans-serif;font-weight:700;font-size:33px;letter-spacing:.5px}
.offer-body{position:absolute;left:29px;top:261px;width:312px;font-size:17.5px;line-height:21px;letter-spacing:-0.4px}
.offer-body .price{margin-bottom:20px}
.offer-body p+p{margin-top:20px}
.rule{position:absolute;left:29px;top:493px;width:312px;height:2px;background:rgba(255,255,255,.8)}
.bank{position:absolute;left:29px;top:507px;font-size:13px;line-height:19px}
.bank strong{font-weight:600}
.address{position:absolute;left:23px;top:1161px;color:var(--white);font-size:19px}
.contact{position:absolute;right:54px;top:1097px;text-align:right;color:var(--white);font-size:14px;line-height:18.8px;letter-spacing:.3px}
</style>
</head>
<body>
<div class="flyer">
  <svg class="shapes" width="913" height="1200" viewBox="0 0 913 1200" aria-hidden="true">
    <defs>
      <radialGradient id="footerGlow" cx="0.5" cy="0.7" r="0.45">
        <stop offset="0" stop-color="#3c3c3c"/>
        <stop offset="1" stop-color="#111111"/>
      </radialGradient>
    </defs>
    <path d="M0 0H913V430H0Z" fill="var(--white)"/>
    <path d="M0 318Q200 292 430 322L430 360Q210 330 0 372Z" fill="#dcdcdc"/>
    <path d="M0 372Q210 330 430 360L430 372Q200 350 0 420Z" fill="var(--paper)"/>
    <path d="M0 420Q150 360 430 350L430 362Q180 378 0 430Z" fill="var(--red)"/>
    <path d="M0 430Q180 378 430 362L430 440H0Z" fill="var(--paper)"/>
    <circle cx="694" cy="197" r="268" fill="var(--red)"/>
    <circle cx="700" cy="203" r="262" fill="var(--white)"/>
    <circle cx="694" cy="197" r="252" fill="var(--grey)"/>
    <circle cx="694" cy="197" r="244" fill="var(--white)"/>
    <path d="M0 1010Q160 1088 420 1076Q700 1064 913 1022L913 1050Q700 1090 420 1094Q150 1100 0 1040Z" fill="var(--red)"/>
    <path d="M0 1060Q150 1118 420 1110Q700 1100 913 1062L913 1200H0Z" fill="url(#footerGlow)"/>
  </svg>

  <div class="brand"><span class="brand-dot"></span>Tavo Toys</div>
  <div class="tagline">Have you been there?</div>

  <div class="photo photo-kids" role="img" aria-label="Photo of smiling children of different backgrounds lying in a circle on green grass"></div>
  <div class="photo photo-baby" role="img" aria-label="Photo of a laughing baby holding a yellow plush chick"></div>

  <div class="intro">
    <div class="name">MIRA LENZ,</div>
    <div>einzelunternehmen / Family business</div>
    <div>Innovative Developer for Plush Toys</div>
    <div>International Trader for Toys</div>
  </div>

  <div class="about">
    <p><span class="line end">We live and work in Bergheim near to Cologne Germany.</span><span class="line end">We speak German and English.</span></p>
    <p><span class="line">The toys are made in China, we are small family business,</span><span class="line">but we are professional in Plush toys business, right</span><span class="line">now we have successfully launched Projects with a</span><span class="line end">huge Japanese 100 Yen Chain Store.</span></p>
  </div>

  <div class="photo photo-sofa" role="img" aria-label="Illustration of six cartoon plush animals sitting on a green sofa"></div>

  <section class="offer">
    <div class="offer-title">PLUSH TOY</div>
    <div class="offer-body">
      <div class="price">100 Yen = 0.90 USD</div>
      <p><span class="line">Our products can meet strictest Quality</span><span class="line">Control, but are with extremely Low</span><span class="line">Price to fit for Japanese Dollar Shop as</span><span class="line">well as his overseas Store around the</span><span class="line end">world.</span></p>
      <p><span class="line">Of course our products are fit for</span><span class="line end">Premium Store too.</span></p>
    </div>
    <div class="rule"></div>
    <div class="bank">
      <strong>Bank information:</strong><br>
      Kontoinhaber/Account Holder: Lena Hartmann<br>
      IBAN: DE12 3456 7890 1234 5678 00<br>
      BIC : TESTDEFF100
    </div>
  </section>
  <div class="photo photo-plush" role="img" aria-label="Photo of a row of colourful plush animal toy samples"></div>

  <div class="address">Lindenweg 8, 50126 Bergheim Germany</div>
  <div class="contact">
    hello@plushwerk.de<br>
    Fon &nbsp; +49 (0) 2271- 555 0142<br>
    Fax &nbsp; +49 (0) 2271- 555 0143<br>
    Mobil: &nbsp;+49 (0) 170 5550 186<br>
    Ust-IdNr./VAT No. DE000111222
  </div>
</div>
</body>
</html>
```